Stationery Design Project for Nimbora, Chicago

Nimbora, a street parking application which helps car drivers find a street parking spot by offering an ideal path along which to look for parking. This path is calculated by our algorithm based on data (e.g. historical data, baseball games schedule, etc.). Along this path the driver will find a spot and will also save 70% of the search time. Customer we target is reg. between 21 and 45 yo.

We envision something young, fresh, bright and original. Slightly abstract maybe. It should represent the idea and elements of finding street parking in the city, e.g. car(s), parking spot, people, city, etc. (just ideas!).

Logo is attached.

Requirement:
- Business Cards (2 Sided Full Color CMYK)
- Letterhead (1 Sided Full Color CMYK)
- Envelope (1 Sided Full Color CMYK)
- Sticker (1 Sided Full Color CMYK), round with a 2inch diameter.

Reason: We're starting to get more and more designs and need more time to look into all of them. Very exciting!! Thanks to everybody!

Hi all, we're in the process of selecting our favs. Though choices!!! Really good submissions. Will keep you posted and sorry for the delay.

Target Market(s)

Car drivers and owners between 21 and 45

Industry/Entity Type

Parking

Requirements
Must have
• Sticker should be round and include company URL nimbora.com and the new logo which we will attach soon.
Should not have
• Should not be too serious or boring.

```html
<!DOCTYPE html>
<html lang="en">
<head>
<meta charset="utf-8">
<title>Nimbora Business Card</title>
<link rel="stylesheet" href="https://fonts.googleapis.com/css2?family=Open+Sans:wght@400;600;700&display=swap">
<style>
  :root {
    --backdrop: #e4e6e9;
    --navy-deep: #131c5e;
    --navy: #0f3f78;
    --teal: #0d6d93;
    --wave-shadow: #5d6063;
    --paper: #ffffff;
    --ink: #444649;
    --ink-dark: #232427;
    --name-blue: #1b2d8e;
    --title-cyan: #17a6de;
    --disc: #1f5fcf;
    --disc-glow: #1a4f94;
  }
  * { margin: 0; padding: 0; box-sizing: border-box; }
  html, body { width: 954px; height: 1200px; overflow: hidden; }
  body {
    background: var(--backdrop);
    font-family: "Open Sans", Arial, sans-serif;
    position: relative;
  }
  .card {
    position: absolute;
    left: 93px;
    width: 797px;
    height: 455px;
    border-radius: 28px;
    overflow: hidden;
    background: var(--paper);
    box-shadow: 0 4px 12px rgba(0,0,0,0.25);
  }
  .card--front { top: 80px; }
  .card--back { top: 628px; }
  .card__art { position: absolute; inset: 0; width: 797px; height: 455px; }
  .wordmark {
    position: absolute;
    right: 50px;
    top: 28px;
    font-size: 60px;
    font-weight: 600;
    color: var(--ink-dark);
    letter-spacing: 1px;
  }
  .person {
    position: absolute;
    right: 42px;
    top: 180px;
    text-align: right;
  }
  .person__name { font-size: 24px; font-weight: 700; color: var(--name-blue); line-height: 30px; }
  .person__title { font-size: 19px; font-weight: 700; color: var(--title-cyan); line-height: 26px; }
  .contacts {
    position: absolute;
    right: 36px;
    top: 300px;
    list-style: none;
    text-align: right;
    font-size: 19px;
    color: var(--ink);
    line-height: 33px;
  }
  .contacts b { font-weight: 700; }
  .address {
    position: absolute;
    left: 92px;
    width: 300px;
    top: 372px;
    text-align: center;
    color: var(--paper);
    font-size: 18px;
    line-height: 26px;
  }
  .web {
    position: absolute;
    right: 36px;
    bottom: 36px;
    font-size: 24px;
    color: var(--ink);
  }
</style>
</head>
<body>

<section class="card card--front">
  <svg class="card__art" viewBox="0 0 797 455" aria-hidden="true">
    <defs>
      <linearGradient id="panelFront" x1="0" y1="0" x2="1" y2="0.4">
        <stop offset="0" stop-color="var(--navy-deep)"/>
        <stop offset="0.45" stop-color="var(--navy)"/>
        <stop offset="1" stop-color="var(--teal)"/>
      </linearGradient>
      <radialGradient id="discFront" cx="0.45" cy="0.4" r="0.6">
        <stop offset="0" stop-color="#3aa0f0"/>
        <stop offset="1" stop-color="var(--disc)"/>
      </radialGradient>
    </defs>
    <path class="wave-shadow" d="M0,0 H500 C452,60 440,150 458,235 C476,320 500,410 478,455 H0 Z" fill="var(--wave-shadow)"/>
    <path class="wave-panel" d="M0,0 H482 C436,60 428,150 446,235 C464,320 488,410 452,455 H0 Z" fill="url(#panelFront)"/>
    <circle cx="247" cy="178" r="150" fill="var(--disc-glow)" opacity="0.45"/>
    <circle cx="247" cy="178" r="128" fill="url(#discFront)"/>
  </svg>
  <div class="wordmark">Nimbora</div>
  <div class="person">
    <p class="person__name">Your Name</p>
    <p class="person__title">Designation</p>
  </div>
  <ul class="contacts">
    <li><b>t</b> : 123-456-7890</li>
    <li><b>c</b> : 123-456-7890</li>
    <li><b>e</b> : name@website.com</li>
    <li><b>w</b> : www.website.com</li>
  </ul>
  <p class="address">City Name, Street Name<br>State Name, Country Code</p>
</section>

<section class="card card--back">
  <svg class="card__art" viewBox="0 0 797 455" aria-hidden="true">
    <defs>
      <linearGradient id="panelBack" x1="0" y1="0" x2="1" y2="0.4">
        <stop offset="0" stop-color="var(--navy-deep)"/>
        <stop offset="0.45" stop-color="var(--navy)"/>
        <stop offset="1" stop-color="var(--teal)"/>
      </linearGradient>
      <radialGradient id="discBack" cx="0.45" cy="0.4" r="0.6">
        <stop offset="0" stop-color="#3aa0f0"/>
        <stop offset="1" stop-color="var(--disc)"/>
      </radialGradient>
    </defs>
    <path class="wave-shadow" d="M0,0 H500 C452,60 440,150 458,235 C476,320 500,410 478,455 H0 Z" fill="var(--wave-shadow)"/>
    <path class="wave-panel" d="M0,0 H482 C436,60 428,150 446,235 C464,320 488,410 452,455 H0 Z" fill="url(#panelBack)"/>
    <circle cx="247" cy="170" r="150" fill="var(--disc-glow)" opacity="0.45"/>
    <circle cx="247" cy="170" r="128" fill="url(#discBack)"/>
  </svg>
  <p class="web">www.website.com</p>
</section>

</body>
</html>
```